Veterinary Pylon

My veterinary clinic is not clearly visible from the street and I want to place a Pylon next to my driveway. I want a modern, elegant straight Design, the Photo shows the sheduled place. One can see the clinic on our Homepage: www.tailbright-vethaus.at
The last pictures are examples for pylones I like

Target Market(s)

the passing cars often miss my entry...I want to show where to turn left

Colors
3276b5
33a6d7
00a990

Requirements
Must have
• High value, simple elegance, size: 250cm (high) x 100cm (width)
Nice to have
• Our Logo, arrow(?)

A special Text is not necessary but this will be an option:

Biegen sie hier ab und wir biegen es wieder hin!
Should not have
• Too much Color, the colors I have chosen are the possible colors but it‘s not necessary to use them.

```html
<!DOCTYPE html>
<html lang="de">
<head>
<meta charset="utf-8">
<title>Tailbright Vethaus – Pylon</title>
<link href="https://fonts.googleapis.com/css2?family=Montserrat:wght@500;600;700;800&display=swap" rel="stylesheet">
<style>
  :root {
    --pylon-blue: #284a8d;
    --accent-cyan: #3fb6df;
    --text-white: #ffffff;
    --backdrop: #e9edf2;
  }
  * { margin: 0; padding: 0; box-sizing: border-box; }
  html, body { width: 818px; height: 1200px; overflow: hidden; }
  body {
    background: var(--backdrop);
    font-family: "Montserrat", sans-serif;
    color: var(--text-white);
    position: relative;
  }
  .pylon-shape {
    position: absolute; left: 0; top: 0;
    width: 818px; height: 1200px;
  }
  .pylon-shape path { fill: var(--pylon-blue); }
  .brand-name {
    position: absolute; left: 155px; width: 507px; top: 360px;
    text-align: center;
    font-weight: 800;
    font-size: 50px;
    line-height: 1.15;
    letter-spacing: 2px;
    text-transform: uppercase;
  }
  .headline {
    position: absolute; left: 248px; top: 584px;
    font-weight: 600;
    font-size: 35px;
    line-height: 45px;
  }
  .hours {
    position: absolute; left: 249px; top: 750px;
    list-style: none;
  }
  .hours-group {
    border-left: 2px solid var(--text-white);
    padding-left: 10px;
    margin-bottom: 18px;
    height: 64px;
  }
  .hours-day {
    color: var(--accent-cyan);
    font-weight: 600;
    font-size: 16px;
    line-height: 20px;
    text-transform: uppercase;
  }
  .hours-time {
    font-weight: 500;
    font-size: 16.5px;
    line-height: 21px;
  }
  .website {
    position: absolute; left: 249px; top: 1003px;
    font-weight: 600;
    font-size: 21px;
  }
</style>
</head>
<body>
  <svg class="pylon-shape" viewBox="0 0 818 1200" aria-hidden="true">
    <path d="M155 326 Q409 280 662 326 L662 537 L616 537 L616 1126 L200 1126 L200 537 L155 537 Z"/>
  </svg>

  <div class="brand-name">Tailbright<br>Vethaus</div>

  <h1 class="headline">Biegen Sie ein,<br>dann biegen wir<br>es hin!</h1>

  <ul class="hours">
    <li class="hours-group">
      <div class="hours-day">Monday - Friday</div>
      <div class="hours-time">08:00 - 12:00</div>
      <div class="hours-time">14:00 - 19:00</div>
    </li>
    <li class="hours-group">
      <div class="hours-day">Saturday</div>
      <div class="hours-time">08:00 - 12:00</div>
      <div class="hours-time">17:00 - 18:00</div>
    </li>
    <li class="hours-group">
      <div class="hours-day">Sunday</div>
      <div class="hours-time">10:00 am - 11:00 am</div>
      <div class="hours-time">17:00 - 18:00</div>
    </li>
  </ul>

  <div class="website">www.tailbright-vethaus.at</div>
</body>
</html>
```